New Business Card Design for Manufacturing

We are an engineering/manufacturing company that offers Advanced machining/assembly/engineering services, as well as innovative products for the heavy duty engine cooling markets.

We are looking to get a new business card designed that is clean and modern looking, but still fits the wide range of technical/skilled work we do.

- We hope to use this design as the base for other design work in new Presentations, web, and print work.

Industry/Entity Type

Engineering

Contact Information for Business Card

Our preferred color of blue is (RGB) 22/71/159 but can vary slightly from that color. Our content will be our Logo and full company name (Vantrell Forge Works, Inc.), company address, name, job title, phone number with extension, cell number, fax number, website, and email address on the cards.
We'd like the full company name next to the logo, but we are open to other interpretations of that layout.
Preferably, we would like the back side to be clean with just our logo, and the front to contain all of the contact information.

Colors
2f74b4
0355a3
85abd2

Requirements
Must have
• - Logo, company name, needed content - We are open to interpretation beyond that.
• - Standard size business card.
• - Horizontal orientation.
• - Enough space for lengthy names / job titles (for example, a job title could read "Directory of Human Resources" or "V.P. of Governmental Affairs"). We need this to look clean, whether the title be short (CEO) or long (as described above).

```html
<!DOCTYPE html>
<html lang="en">
<head>
<meta charset="utf-8">
<title>Vantrell Forge Works – Business Card</title>
<link rel="stylesheet" href="https://fonts.googleapis.com/css2?family=Oswald:wght@500;600&family=Open+Sans:wght@400&display=swap">
<style>
  :root {
    --backdrop: #e3e2e0;
    --card: #f7f7f5;
    --card-edge: #d2ac2a;
    --brand-blue: #16479f;
    --ink-grey: #8a8a8a;
    --rule-grey: #b5b5b5;
  }
  * { margin: 0; padding: 0; box-sizing: border-box; }
  html, body {
    width: 1200px;
    height: 720px;
    overflow: hidden;
    background: var(--backdrop);
  }
  .canvas {
    width: 1200px;
    height: 720px;
    display: flex;
    flex-direction: column;
    align-items: center;
    justify-content: center;
    gap: 40px;
  }
  .card {
    position: relative;
    width: 440px;
    height: 252px;
    background: var(--card);
    border-bottom: 3px solid var(--card-edge);
    box-shadow: 0 2px 6px rgba(0,0,0,0.12);
  }
  /* Back side: brand name only */
  .card--back {
    display: flex;
    align-items: center;
    justify-content: center;
  }
  .brand-name {
    font-family: "Oswald", sans-serif;
    font-weight: 600;
    font-size: 30px;
    letter-spacing: 1px;
    color: var(--brand-blue);
    text-transform: uppercase;
  }
  /* Front side: contact details */
  .card--front .identity-row {
    position: absolute;
    top: 106px;
    left: 0;
    right: 0;
    display: flex;
    justify-content: center;
    align-items: center;
    gap: 12px;
  }
  .person {
    text-align: right;
  }
  .person__name {
    font-family: "Oswald", sans-serif;
    font-weight: 500;
    font-size: 21px;
    line-height: 1;
    color: var(--brand-blue);
    text-transform: uppercase;
  }
  .person__title {
    font-family: "Open Sans", sans-serif;
    font-size: 9px;
    color: var(--ink-grey);
    margin-top: 3px;
  }
  .divider {
    width: 1px;
    height: 38px;
    background: var(--rule-grey);
  }
  .contact-list {
    list-style: none;
    font-family: "Open Sans", sans-serif;
    font-size: 9.5px;
    color: var(--ink-grey);
    line-height: 13px;
  }
  .contact-list li {
    display: flex;
    align-items: center;
    gap: 8px;
  }
  .contact-list svg {
    width: 8px;
    height: 8px;
    fill: none;
    stroke: var(--brand-blue);
    stroke-width: 1.6;
  }
  .address {
    position: absolute;
    bottom: 36px;
    left: 0;
    right: 0;
    text-align: center;
    font-family: "Open Sans", sans-serif;
    font-size: 9.5px;
    color: var(--ink-grey);
  }
</style>
</head>
<body>
<main class="canvas">
  <section class="card card--back" aria-label="Card back">
    <span class="brand-name">Vantrell Forge</span>
  </section>

  <section class="card card--front" aria-label="Card front">
    <div class="identity-row">
      <div class="person">
        <p class="person__name">Marcus Delane</p>
        <p class="person__title">V.P. of Governmental Affairs</p>
      </div>
      <span class="divider"></span>
      <ul class="contact-list">
        <li>
          <svg viewBox="0 0 10 10" aria-hidden="true"><path d="M2 1.5 L3.8 1.5 L4.4 3.4 L3.3 4.2 C3.9 5.5 4.6 6.2 5.8 6.8 L6.6 5.7 L8.5 6.3 L8.5 8.1 C5 8.3 1.8 5 2 1.5 Z"/></svg>
          +999 9999 9999
        </li>
        <li>
          <svg viewBox="0 0 10 10" aria-hidden="true"><rect x="1" y="2.2" width="8" height="5.6" rx="0.6"/><path d="M1 2.6 L5 5.6 L9 2.6"/></svg>
          info@mywebsite.com
        </li>
        <li>
          <svg viewBox="0 0 10 10" aria-hidden="true"><circle cx="5" cy="5" r="4"/><path d="M1 5 H9 M5 1 C3 3.5 3 6.5 5 9 M5 1 C7 3.5 7 6.5 5 9"/></svg>
          www.mywebsite.com
        </li>
      </ul>
    </div>
    <p class="address">99th Street, Exact Road, New cross side, CA 456982.</p>
  </section>
</main>
</body>
</html>
```